High-end Oceanfront Real Estate Group Needs Clean, Modern Web Design

I’m looking for a clean, professional, modern and beautiful homepage web design for a Real Estate group in Southern California, USA.

The group/company is “Marwick on the Shore,” and they specialize in high end (i.e. expensive), oceanfront real estate in the Orange County area.

The look and feel of the page should accentuate the brand qualities: luxurious/expensive, professional, and beautiful (Orange County is one of the most beautiful areas in all the US and we would love the site to emphasize the beautiful beaches and scenery it has to offer).

Looks we like:
• www.brantleyhomesrealty.example
• www.closedbyvane.example -- I think the design is pretty out-dated in this site, but I like the organization/layout of the site

Header Tags (I don’t know if we can fit all of these, may need a side-menu, but I’d prefer header title only if possible):
• Welcome
• Featured Listings
• Previously Sold
• Sell
• Property Search
• Team
• Videos
• Blog
• Explore O.C.
• Contact

I have attached the beach and logo pics that we would like to use as the header, a few pictures of the team, and one sample home/view pic which can be used in any of the other sections (for pictures of the homes, just find expensive oceanfront houses and that will be fine).

I promise to provide feedback to each and every design submission. I appreciate the hard work that all of you are putting into your designs. There can be only one contest winner, but I hope to give all of you helpful feedback to submit the best designs possible!

Target Market(s)

Very wealthy home owners of oceanfront properties. These properties are worth several millions of dollars, and thus the site and brand needs to be targeted to very wealthy, successful individuals and families (both US and international buyers).

Industry/Entity Type

Real Estate

Number of Pages Required

2 page

Requirements
Must have
• I don’t want to give too many requirements, because I want to let you all be creative. However, here are the few Must Haves:
• Must submit 2 page designs (a home page and a sub page)
• Must use logo provided
• Focus is mostly on homes, but I would like to include some beach/ocean imagery as well
• The first “item” on the home page should be an accordion/slider which shows pictures of homes and with 1 line of text: “List with the Leader” and two link buttons: “Sell Your Home” and “Buy Your Home”
• Color palette needs to be mainly blues--to match ocean and sky blue
• Exported in all major formats (psd,ai,eps,png,jpeg,etc)
Nice to have
• We don’t necessarily need all of these, but would like to feature most:
• List of videos
• “Meet the Team”—brief team bios and pics
• Link(s) to Blog
• “List with the Leader” – section on why they should choose this firm
• Featured Listings
• Previously Sold

```html
<!DOCTYPE html>
<html lang="en">
<head>
<meta charset="utf-8">
<title>Marwick on the Shore — Oceanfront Real Estate</title>
<link href="https://fonts.googleapis.com/css2?family=Raleway:wght@400;500;600;700&family=Open+Sans:wght@400;600&display=swap" rel="stylesheet">
<style>
:root{
  --blue:#1f6fbf;
  --blue-dark:#17569a;
  --ink:#2c2c2c;
  --muted:#7a7a7a;
  --line:#e4e4e4;
  --band:#2f2f2f;
  --footer:#2b2b2b;
  --footer-deep:#1f1f1f;
  --white:#ffffff;
  --soft:#f7f7f7;
}
*{box-sizing:border-box;margin:0;padding:0}
html,body{width:1200px;height:2852px;overflow:hidden}
body{position:relative;background:var(--white);font-family:"Open Sans",Arial,sans-serif;color:var(--ink)}
.abs{position:absolute}

/* header */
.site-header{left:0;top:0;width:1200px;height:68px;background:var(--white);z-index:3;box-shadow:0 1px 3px rgba(0,0,0,.08)}
.logo-box{left:112px;top:0;width:272px;height:248px;background:var(--white);z-index:4;display:flex;flex-direction:column;justify-content:center;align-items:center;box-shadow:0 2px 10px rgba(0,0,0,.15)}
.logo-name{font-family:"Raleway",sans-serif;font-weight:600;color:var(--blue);font-size:40px;line-height:1.1;text-align:center;text-transform:uppercase;letter-spacing:2px}
.main-nav{left:360px;top:0;height:68px;display:flex;gap:0;align-items:stretch}
.main-nav a{display:flex;align-items:center;padding:0 22px;font-family:"Raleway",sans-serif;font-weight:600;font-size:15px;color:#555;text-decoration:none;letter-spacing:.5px}
.main-nav a.is-active{background:var(--blue);color:var(--white)}

/* hero */
.hero{left:0;top:68px;width:1200px;height:512px;background:linear-gradient(180deg,#8fc3ea 0%,#bfe0f5 34%,#3d84b8 46%,#dfe6ea 60%,#f1efec 78%,#c9c2ba 100%)}
.hero-caption{left:112px;top:290px}
.hero-line{display:inline-block;background:rgba(20,40,60,.55);color:var(--white);font-family:"Raleway",sans-serif;font-weight:600;font-size:40px;letter-spacing:1px;padding:6px 16px;margin-bottom:10px;text-transform:uppercase}

/* welcome */
.welcome{left:0;top:600px;width:1200px;text-align:center}
.welcome h1{font-family:"Raleway",sans-serif;font-weight:500;font-size:34px;color:var(--ink);margin-top:22px;letter-spacing:1px}
.welcome h1 strong{color:var(--blue);font-weight:700}
.welcome p{width:760px;margin:20px auto 0;font-size:15px;line-height:26px;color:var(--muted)}
.btn-row{margin-top:38px;display:flex;justify-content:center;gap:20px}
.btn{display:inline-block;padding:14px 28px;font-family:"Raleway",sans-serif;font-weight:600;font-size:17px;border:2px solid var(--blue);text-decoration:none}
.btn-solid{background:var(--blue);color:var(--white)}
.btn-ghost{background:var(--white);color:var(--blue)}

/* featured */
.featured-band{left:0;top:932px;width:1200px;height:260px;background:var(--band)}
.featured-tab{left:466px;top:888px;width:268px;height:64px;background:var(--band);border-radius:6px 6px 0 0;color:var(--white);font-family:"Raleway",sans-serif;font-weight:500;font-size:30px;text-align:center;line-height:64px}
.listing{top:968px;width:232px}
.listing-photo{height:170px}
.listing-caption{height:34px;background:var(--white);font-size:13px;color:#555;text-align:center;line-height:34px}
.arrow-btn{top:1040px;width:28px;height:36px;background:#eee}

/* section titles */
.section-title{left:0;width:1200px;text-align:center;font-family:"Raleway",sans-serif;font-weight:500;font-size:38px;color:var(--ink)}

/* team */
.member{top:1340px;width:200px;text-align:center}
.member-photo{width:116px;height:116px;border-radius:50%;margin:0 auto;border:4px solid var(--white);box-shadow:0 0 0 2px var(--line)}
.member-name{margin-top:20px;font-family:"Raleway",sans-serif;font-weight:700;font-size:13px;text-transform:uppercase;color:var(--ink)}
.member-role{margin-top:4px;font-size:12px;color:var(--muted)}

/* videos */
.videos-band{left:0;top:1600px;width:1200px;height:480px;background:linear-gradient(90deg,#b5733c 0%,#6c8fae 30%,#3d6a96 60%,#c28952 100%)}
.videos-panel{left:80px;top:1632px;width:1040px;height:372px;background:var(--white)}
.video{top:1742px;width:222px;height:164px}
.play{width:60px;height:60px}

/* testimonials */
.quote-card{top:2172px;width:440px;height:230px;background:var(--soft);border:1px solid var(--line);padding:34px 44px 0;text-align:center}
.quote-mark{left:20px;top:14px;font-family:"Raleway",sans-serif;font-size:56px;color:var(--blue);line-height:1}
.quote-text{font-size:15px;line-height:25px;color:#555;font-style:italic}
.quote-avatar{width:78px;height:78px;border-radius:50%;border:3px solid var(--white);box-shadow:0 0 0 1px var(--line)}
.quote-author{width:440px;text-align:center;font-size:14px;color:#555;top:2470px}

/* footer */
.site-footer{left:0;top:2532px;width:1200px;height:276px;background:var(--footer)}
.footer-col{top:2562px;color:#bdbdbd;font-size:12px;line-height:20px}
.footer-col h4{color:var(--white);font-family:"Raleway",sans-serif;font-weight:600;font-size:15px;margin-bottom:12px}
.social-row{display:flex;gap:10px;margin-bottom:22px}
.social-row span{width:28px;height:28px;background:var(--blue);border-radius:3px}
.newsletter{display:flex;margin-top:10px}
.newsletter .field{width:180px;height:32px;background:var(--white);color:#999;font-size:11px;line-height:32px;padding-left:10px}
.newsletter .go{width:90px;height:32px;background:var(--blue);color:var(--white);font-size:11px;line-height:32px;text-align:center}
.footer-bar{left:0;top:2808px;width:1200px;height:44px;background:var(--footer-deep);display:flex;align-items:center;justify-content:space-between;padding:0 112px;color:#bbb;font-size:11px}
.footer-bar nav{display:flex;gap:26px;font-family:"Raleway",sans-serif;font-weight:600;color:var(--white)}
</style>
</head>
<body>

<header class="abs site-header">
  <nav class="abs main-nav">
    <a class="is-active">HOME</a><a>FEATURED LISTINGS</a><a>SOLD</a><a>SELL</a><a>TEAM</a><a>VIDEOS</a><a>BLOG</a><a>CONTACT</a>
  </nav>
</header>
<div class="abs logo-box"><div class="logo-name">Marwick<br>on the<br>Shore</div></div>

<section class="abs hero" role="img" aria-label="Bright oceanfront living room with a wide window over the sea and coastline"></section>
<div class="abs hero-caption">
  <div class="hero-line">We are offering</div><br>
  <div class="hero-line">The best real estate deals</div>
</div>

<section class="abs welcome">
  <h1>WELCOME TO <strong>MARWICK ON THE SHORE</strong></h1>
  <p>Lorem ipsum dolor sit amet, consectetur adipiscing elit, sed do eiusmod tempor incididunt ut labore et dolore magna aliqua. Ut enim ad minim veniam, quis nostrud exercitation ullamco laboris nisi ut aliquip ex ea commodo consequat.</p>
  <div class="btn-row"><a class="btn btn-solid">Sell Your Home</a><a class="btn btn-ghost">Buy Your Home</a></div>
</section>

<div class="abs featured-band"></div>
<div class="abs featured-tab">Feature Listing</div>
<div class="abs arrow-btn" style="left:78px"><svg width="28" height="36" viewBox="0 0 28 36"><path d="M17 11l-7 7 7 7" fill="none" stroke="#555" stroke-width="2.5"/></svg></div>
<div class="abs arrow-btn" style="left:1094px"><svg width="28" height="36" viewBox="0 0 28 36"><path d="M11 11l7 7-7 7" fill="none" stroke="#555" stroke-width="2.5"/></svg></div>
<article class="abs listing" style="left:112px"><div class="listing-photo" role="img" aria-label="Coastal villa above a turquoise bay" style="background:linear-gradient(180deg,#6fb4e0,#2f8fb5 55%,#c8b48a)"></div><div class="listing-caption">Family villa in Ottawa</div></article>
<article class="abs listing" style="left:360px"><div class="listing-photo" role="img" aria-label="Stone villa courtyard with arched doorway" style="background:linear-gradient(180deg,#c99a5e,#8a6a45 60%,#5b4a35)"></div><div class="listing-caption">A bedroom villa in Victoria</div></article>
<article class="abs listing" style="left:608px"><div class="listing-photo" role="img" aria-label="Luxury apartment complex with a pool at dusk" style="background:linear-gradient(180deg,#2d3f6e,#c9874a 55%,#3b78a8)"></div><div class="listing-caption">Luxury apartment in Toronto</div></article>
<article class="abs listing" style="left:856px"><div class="listing-photo" role="img" aria-label="Cottage on a cliff over blue water" style="background:linear-gradient(180deg,#7cc0ea,#2b86c4 60%,#d9d3c3)"></div><div class="listing-caption">Great cottage in Virginia</div></article>

<h2 class="abs section-title" style="top:1250px">Our Team</h2>
<div class="abs member" style="left:100px"><div class="member-photo" role="img" aria-label="Portrait of Alina Reyes" style="background:#c9b3a0"></div><div class="member-name">Alina Reyes</div><div class="member-role">Lorem ipsum amet adipiscing</div></div>
<div class="abs member" style="left:300px"><div class="member-photo" role="img" aria-label="Portrait of Tessa Moreno" style="background:#a88a74"></div><div class="member-name">Tessa Moreno</div><div class="member-role">Lorem ipsum amet adipiscing</div></div>
<div class="abs member" style="left:500px"><div class="member-photo" role="img" aria-label="Portrait of Daniel Whitcomb" style="background:#8d8f93"></div><div class="member-name">Daniel Whitcomb</div><div class="member-role">Lorem ipsum amet adipiscing</div></div>
<div class="abs member" style="left:700px"><div class="member-photo" role="img" aria-label="Portrait of Nora Hartley" style="background:#c8ad8c"></div><div class="member-name">Nora Hartley</div><div class="member-role">Lorem ipsum amet adipiscing</div></div>
<div class="abs member" style="left:900px"><div class="member-photo" role="img" aria-label="Portrait of Elise Carrow" style="background:#b59a86"></div><div class="member-name">Elise Carrow</div><div class="member-role">Lorem ipsum amet adipiscing</div></div>

<section class="abs videos-band" role="img" aria-label="Evening view of a coastal city street"></section>
<div class="abs videos-panel"></div>
<h2 class="abs section-title" style="top:1656px">Latest Videos</h2>
<div class="abs video" style="left:112px" role="img" aria-label="Video thumbnail of a resort pool by the sea"><div style="width:100%;height:100%;background:linear-gradient(180deg,#7cc5ea,#2d9bc6 55%,#d8c59a)"></div></div>
<div class="abs video" style="left:362px" role="img" aria-label="Video thumbnail of a historic amphitheatre"><div style="width:100%;height:100%;background:linear-gradient(180deg,#8fbbe0,#b08a5c 60%,#7a5f40)"></div></div>
<div class="abs video" style="left:612px" role="img" aria-label="Video thumbnail of a family on the beach"><div style="width:100%;height:100%;background:linear-gradient(180deg,#9fd0ee,#e2c79b 60%,#c49a6c)"></div></div>
<div class="abs video" style="left:862px" role="img" aria-label="Video thumbnail of friends relaxing outdoors"><div style="width:100%;height:100%;background:linear-gradient(180deg,#b8d7ea,#d6a57a 55%,#8e7156)"></div></div>
<svg class="abs play" style="left:193px;top:1794px" viewBox="0 0 60 60"><circle cx="30" cy="30" r="28" fill="rgba(255,255,255,.35)" stroke="#fff" stroke-width="3"/><path d="M24 18l18 12-18 12z" fill="#fff"/></svg>
<svg class="abs play" style="left:443px;top:1794px" viewBox="0 0 60 60"><circle cx="30" cy="30" r="28" fill="rgba(255,255,255,.35)" stroke="#fff" stroke-width="3"/><path d="M24 18l18 12-18 12z" fill="#fff"/></svg>
<svg class="abs play" style="left:693px;top:1794px" viewBox="0 0 60 60"><circle cx="30" cy="30" r="28" fill="rgba(255,255,255,.35)" stroke="#fff" stroke-width="3"/><path d="M24 18l18 12-18 12z" fill="#fff"/></svg>
<svg class="abs play" style="left:943px;top:1794px" viewBox="0 0 60 60"><circle cx="30" cy="30" r="28" fill="rgba(255,255,255,.35)" stroke="#fff" stroke-width="3"/><path d="M24 18l18 12-18 12z" fill="#fff"/></svg>

<h2 class="abs section-title" style="top:2076px">Customer Testimonials</h2>
<div class="abs quote-card" style="left:120px"><span class="abs quote-mark">“</span><p class="quote-text">"I love that Marwick offer the book online feature. It saves me time from my schedule and it is so easy to do! If you are looking for a trusted and thorough cleaner, look no further!"</p></div>
<div class="abs quote-card" style="left:640px"><span class="abs quote-mark">“</span><p class="quote-text">"I love that Marwick offer the book online feature. It saves me time from my schedule and it is so easy to do! If you are looking for a trusted and thorough cleaner, look no further!"</p></div>
<div class="abs quote-avatar" style="left:301px;top:2366px;background:#c7d9a3" role="img" aria-label="Customer portrait"></div>
<div class="abs quote-avatar" style="left:821px;top:2366px;background:#6b6b6b" role="img" aria-label="Customer portrait"></div>
<div class="abs quote-author" style="left:120px">- Harriet, in Corona -</div>
<div class="abs quote-author" style="left:640px">- Harriet, in Corona -</div>

<footer class="abs site-footer"></footer>
<div class="abs footer-col" style="left:112px;width:200px"><h4>Contact Info</h4>1200 Harbor Lane<br>Suite 210, Newport<br>Orange County, CA<br>Email: info@marwickshore.example<br>Phone: 555-010-2040</div>
<div class="abs footer-col" style="left:360px;width:200px"><h4>About Us</h4>Lorem ipsum dolor sit amet, consectetur adipiscing elit, sed do eiusmod tempor incididunt ut labore et dolore magna aliqua.</div>
<div class="abs footer-col" style="left:590px;width:170px"><h4>Company Info</h4>Lorem ipsum dolor sit amet consectetur adipiscing elit</div>
<div class="abs footer-col" style="left:800px;width:300px"><h4>Stay updates on our Social Network</h4>
  <div class="social-row"><span></span><span></span><span></span></div>
  <h4 style="margin-bottom:0">Join Our Newsletter</h4>
  <div class="newsletter"><div class="field">Enter your email address</div><div class="go">Subscribe</div></div>
</div>
<div class="abs footer-bar"><nav><span>HOME</span><span>ABOUT</span><span>TEAM</span><span>PORTFOLIO</span><span>NEWS</span><span>CONTACT</span></nav><span>© Copyright 2015 All rights Reserved</span></div>

</body>
</html>
```